Marcus & Fiona's Midsummer Unwind Evening

Invitation to a party 60-80 people at a private residence. Age range 30-40s.

Themes: summer/casual/Australian backyard/local community

**For delivery via both email and printed copy**
Would like one document suitable for both purposes or two versions for electronic or paper invitation. I will arrange printing so please prepare it in a suitable format.

Specimen text attached. Address and phone contact to follow by message with successful bidder

Thanks!
Marcus

Target Market(s)

Locals, friends. Party attendees will typicaly be parents in their forties who who be leaving the kids at home for a relaxed party night, and walking home afterward

Industry/Entity Type

Community

Font styles to use
Sans Serif

Requirements
Should not have
• Cliche Australiana imagery. No kangaroos etc

```html
<!DOCTYPE html>
<html lang="en">
<head>
<meta charset="utf-8">
<title>Marcus &amp; Fiona's Midsummer Unwind Evening</title>
<link rel="stylesheet" href="https://fonts.googleapis.com/css2?family=Lato:wght@100;300;400;700&family=Parisienne&display=swap">
<style>
  :root {
    --ink-night: #121132;
    --festive-pink: #e5088f;
    --paper-white: #ffffff;
    --soft-grey: #d6d6de;
  }
  html, body {
    margin: 0;
    padding: 0;
    overflow: hidden;
    background: var(--ink-night);
  }
  .invitation {
    position: relative;
    width: 857px;
    height: 1200px;
    background: var(--ink-night);
    font-family: "Lato", sans-serif;
    overflow: hidden;
  }
  .invitation > * {
    position: absolute;
    left: 0;
    width: 100%;
    margin: 0;
    text-align: center;
  }
  .flourish {
    left: 204px;
    width: 450px;
    border-radius: 60px;
    background: radial-gradient(ellipse at center, rgba(229, 8, 143, 0.55), rgba(229, 8, 143, 0.12) 70%, transparent 100%);
  }
  .flourish--top { top: 48px; height: 146px; }
  .flourish--bottom { top: 1004px; height: 148px; }
  .divider {
    top: 684px;
    left: 160px;
    width: 536px;
    height: 80px;
  }
  .headline {
    top: 278px;
    font-weight: 700;
    font-size: 35px;
    letter-spacing: 0.2px;
    color: var(--festive-pink);
  }
  .subline {
    top: 318px;
    font-weight: 300;
    font-size: 26px;
    color: var(--festive-pink);
  }
  .hosts {
    top: 432px;
    font-weight: 100;
    font-size: 38px;
    letter-spacing: 1px;
    color: var(--soft-grey);
  }
  .event-name {
    top: 478px;
    font-family: "Parisienne", cursive;
    font-size: 48px;
    color: var(--festive-pink);
  }
  .audience {
    top: 547px;
    font-weight: 300;
    font-size: 16px;
    color: var(--soft-grey);
  }
  .time-icon {
    top: 768px;
    left: 399px;
    width: 60px;
    height: 60px;
  }
  .when {
    top: 852px;
    font-weight: 300;
    font-size: 21px;
    color: var(--paper-white);
  }
  .when .sep { margin: 0 18px; }
  .where {
    top: 904px;
    font-weight: 700;
    font-size: 26px;
    color: var(--paper-white);
  }
</style>
</head>
<body>
<main class="invitation">
  <div class="flourish flourish--top" role="img" aria-label="Ornamental pink scrollwork flourish"></div>

  <p class="headline">LEAVE THE KIDS AT HOME</p>
  <p class="subline">and Let Your Hair Down At</p>

  <p class="hosts">Marcus &amp; Fiona’s</p>
  <h1 class="event-name" style="font-weight:400">Midsummer Unwind Evening</h1>
  <p class="audience">For Brindle Heights and friends</p>

  <svg class="divider" viewBox="0 0 536 80" aria-hidden="true">
    <line x1="40" y1="45" x2="496" y2="45" stroke="var(--festive-pink)" stroke-width="3"/>
    <rect x="188" y="5" width="160" height="40" rx="20" fill="var(--festive-pink)" opacity="0.35" role="img" aria-label="Small ornamental scroll"/>
    <circle cx="268" cy="45" r="6" fill="none" stroke="var(--festive-pink)" stroke-width="3"/>
    <circle cx="30" cy="45" r="10" fill="var(--festive-pink)" opacity="0.5"/>
    <circle cx="506" cy="45" r="10" fill="var(--festive-pink)" opacity="0.5"/>
  </svg>

  <svg class="time-icon" viewBox="0 0 60 60" aria-hidden="true">
    <circle cx="28" cy="28" r="23" fill="none" stroke="var(--paper-white)" stroke-width="5"/>
    <path d="M28 14 V29 H40" fill="none" stroke="var(--paper-white)" stroke-width="5" stroke-linecap="round"/>
    <rect x="36" y="36" width="22" height="22" rx="3" fill="var(--ink-night)" stroke="var(--paper-white)" stroke-width="3"/>
    <g fill="var(--paper-white)">
      <circle cx="42" cy="44" r="1.6"/><circle cx="47" cy="44" r="1.6"/><circle cx="52" cy="44" r="1.6"/>
      <circle cx="42" cy="50" r="1.6"/><circle cx="47" cy="50" r="1.6"/><circle cx="52" cy="50" r="1.6"/>
    </g>
  </svg>

  <p class="when">Saturday 2 January<span class="sep">|</span>From 6pm ‘til late</p>
  <p class="where">25 Larkspur Street, Brindle Heights</p>

  <div class="flourish flourish--bottom" role="img" aria-label="Ornamental pink scrollwork flourish"></div>
</main>
</body>
</html>
```